Design a Cover for a Book on Innovation

I need a design for my book: The Quiet Harvest of Invention
It is about the following:

Innovation is not just for those endowed with special talent or skills in technology. This book describes the thought framework that consists of seven principal differences between the current period and the past. Innovation is happening along these shifts. Understanding the differences can allow for consistent innovation and the identification of real opportunities.
Updates

To All: All of you show great talent as designers. I've added a bit more to the description. Feel free to ask questions. Best, DT

Font styles to use
Sans Serif

Colors

Designer to choose colors to be used in the design.

Requirements
Must have
• It should feel modern and innovative. It should incorporate the meaning of Quiet Harvest.
Nice to have
• It should have the title, and a holder spot for the subtitle and author's name Dara Tovens
Should not have
• It should not be overly busy. Sleek modern design that still gets the point across. Alternatively an image that is a full cover graphic.

```html
<!DOCTYPE html>
<html lang="en">
<head>
<meta charset="utf-8">
<title>The Quiet Harvest of Invention — Book Cover</title>
<link rel="stylesheet" href="https://fonts.googleapis.com/css2?family=Jost:wght@400;500&family=Great+Vibes&display=swap">
<style>
  :root {
    --stage: #d9d9d9;
    --paper: #ffffff;
    --ink: #111111;
    --accent-red: #a50f14;
    --band-grey: #646464;
    --rule-grey: #6a6a6a;
    --art-light: #e4e4e4;
    --art-mid: #cfcfcf;
    --art-bulb: #f3ee7a;
    --author-ink: #ffffff;
  }
  * { margin: 0; padding: 0; box-sizing: border-box; }
  html, body {
    width: 1200px; height: 900px; overflow: hidden;
    background: var(--stage);
  }
  .canvas {
    position: relative; width: 1200px; height: 900px;
    background: var(--stage);
  }
  .book-cover {
    position: absolute; left: 340px; top: 0;
    width: 636px; height: 900px;
    background: var(--paper);
    overflow: hidden;
  }
  .top-rule {
    position: absolute; left: 0; width: 100%;
    background: var(--rule-grey);
  }
  .top-rule--thick { top: 0; height: 12px; }
  .top-rule--thin { top: 15px; height: 5px; }

  .cover-art {
    position: absolute; left: 0; top: 55px;
    width: 290px; height: 310px;
  }

  .title {
    font-family: "Jost", "Futura", sans-serif;
    color: var(--ink);
  }
  .title__line { position: absolute; white-space: nowrap; line-height: 1; }
  .title__the {
    right: 40px; top: 212px;
    font-size: 40px; letter-spacing: 0.42em; margin-right: -0.42em;
  }
  .title__quiet {
    right: 40px; top: 258px;
    font-size: 60px; letter-spacing: 0.04em;
  }
  .title__harvest {
    left: 110px; width: 500px; top: 330px; text-align: center;
    font-family: "Great Vibes", cursive;
    font-size: 150px; color: var(--accent-red);
  }
  .title__of-row {
    position: absolute; left: 160px; top: 532px;
    width: 390px; height: 40px;
    display: flex; align-items: center; gap: 8px;
  }
  .title__of-rule { flex: 1; height: 1px; background: var(--ink); }
  .title__of-rule--left { background: linear-gradient(to right, transparent, var(--ink)); }
  .title__of-rule--right { background: linear-gradient(to left, transparent, var(--ink)); }
  .title__of { font-size: 40px; line-height: 1; }
  .title__invention {
    right: 42px; top: 612px;
    font-size: 98px; letter-spacing: -0.01em;
  }

  .author-band {
    position: absolute; left: 0; bottom: 0;
    width: 100%; height: 97px;
    background: var(--band-grey);
    display: flex; align-items: center; justify-content: center;
  }
  .author-name {
    font-family: "Jost", "Futura", sans-serif;
    font-size: 30px; color: var(--author-ink);
    letter-spacing: 0.42em; margin-right: -0.42em;
    text-transform: uppercase;
  }
</style>
</head>
<body>
<div class="canvas">
  <div class="book-cover">
    <div class="top-rule top-rule--thick"></div>
    <div class="top-rule top-rule--thin"></div>

    <svg class="cover-art" viewBox="0 0 290 310" role="img"
         aria-label="Illustration: a light grey branch with leaves, a yellow light bulb hanging from it like fruit, and a grey hand reaching toward it">
      <defs>
        <radialGradient id="artGlow" cx="0.35" cy="0.6" r="0.7">
          <stop offset="0" stop-color="var(--art-bulb)" stop-opacity="0.55"/>
          <stop offset="0.45" stop-color="var(--art-light)"/>
          <stop offset="1" stop-color="var(--paper)"/>
        </radialGradient>
      </defs>
      <rect width="290" height="310" fill="url(#artGlow)"/>
    </svg>

    <h1 class="title">
      <span class="title__line title__the">THE</span>
      <span class="title__line title__quiet">QUIET</span>
      <span class="title__line title__harvest">harvest</span>
      <span class="title__of-row">
        <span class="title__of-rule title__of-rule--left"></span>
        <span class="title__of">OF</span>
        <span class="title__of-rule title__of-rule--right"></span>
      </span>
      <span class="title__line title__invention">INVENTION</span>
    </h1>

    <div class="author-band">
      <p class="author-name">Dara Tovens</p>
    </div>
  </div>
</div>
</body>
</html>
```